Flyer for customer acquisition.

Hello, We are a sportmanagement agency from Germany and we need information flyers for customer acquisition. It should be DinA4 and should have a modern but serious design. I have uploaded a information sheet, where you can find the text and the composition, the flyer should have. I also uploaded Pictures / Images, which you can use. Of course you can use other suitable images. If they are not free, I will buy them later. On the bottom of the flyer there has been the contact information. You will find them in the download section, too. If you have questions, just write me. If I forgot something, I will update the letter :) Thank you very much!
Ich brauche zusätzliche Tage um durchzusehen

```html
<!DOCTYPE html>
<html lang="de">
<head>
<meta charset="utf-8">
<title>VENTRA – Nachwuchsförderung und -management</title>
<link href="https://fonts.googleapis.com/css2?family=Lato:wght@400;700&family=Montserrat:wght@400;500&display=swap" rel="stylesheet">
<style>
  :root {
    --page-bg: #e6e8ea;
    --paper: #ffffff;
    --ink: #1b1b1b;
    --brand-blue: #34a6d6;
    --footer-black: #1c1c1c;
    --footer-blue: #35a8d8;
    --box-border: #2a2a2a;
  }
  * { margin: 0; padding: 0; box-sizing: border-box; }
  html, body { width: 1200px; height: 1200px; overflow: hidden; background: var(--page-bg); }
  body { position: relative; font-family: 'Lato', sans-serif; color: var(--ink); }

  .flyer {
    position: absolute; left: 180px; top: 15px;
    width: 840px; height: 1170px;
    background: var(--paper);
    overflow: hidden;
    box-shadow: 0 2px 12px rgba(0,0,0,0.12);
  }

  .brand-mark {
    position: absolute; left: 40px; top: 70px; width: 335px;
    display: flex; flex-direction: column; align-items: center; gap: 14px;
  }
  .brand-mark__dot { width: 62px; height: 62px; border-radius: 50%; border: 3px solid var(--ink); }
  .brand-mark__name {
    font-family: 'Montserrat', sans-serif; font-weight: 500;
    font-size: 44px; letter-spacing: 1px; color: var(--ink); line-height: 1;
  }

  .headline-brand {
    position: absolute; left: 38px; top: 258px; width: 326px;
    font-family: 'Montserrat', sans-serif; font-weight: 400;
    font-size: 74px; line-height: 1; color: var(--brand-blue); letter-spacing: 0;
    white-space: nowrap;
  }
  .tagline {
    position: absolute; left: 40px; top: 340px; width: 324px;
    font-family: 'Lato', sans-serif; font-weight: 700; font-size: 27px; line-height: 33px;
  }
  .tagline__accent { display: block; text-align: right; color: var(--brand-blue); }

  .claim { position: absolute; left: 40px; top: 462px; }
  .claim__top { font-family: 'Montserrat', sans-serif; font-weight: 500; font-size: 29px; letter-spacing: 0.5px; line-height: 36px; }
  .claim__mid { font-family: 'Lato', sans-serif; font-weight: 700; font-size: 62px; line-height: 62px; color: var(--brand-blue); }
  .claim__bottom { font-family: 'Montserrat', sans-serif; font-weight: 500; font-size: 44px; line-height: 52px; }

  .hero-figure {
    position: absolute; left: 420px; top: 50px; width: 380px; height: 610px;
    border-radius: 40px;
    background:
      radial-gradient(ellipse at 40% 30%, rgba(110,80,220,0.85), transparent 55%),
      radial-gradient(ellipse at 25% 40%, rgba(230,40,160,0.7), transparent 45%),
      radial-gradient(ellipse at 70% 35%, rgba(40,170,230,0.8), transparent 55%),
      radial-gradient(ellipse at 55% 80%, rgba(240,200,60,0.7), transparent 55%),
      #f3f4f8;
  }

  .service { position: absolute; width: 367px; height: 90px; border: 1.5px solid var(--box-border); border-radius: 5px; }
  .service--left { left: 38px; }
  .service--right { left: 431px; }
  .service--row1 { top: 690px; }
  .service--row2 { top: 814px; }
  .service--row3 { top: 935px; }
  .service__title {
    position: absolute; left: 12px; top: -13px; padding: 0 8px;
    background: var(--paper); color: var(--brand-blue);
    font-size: 18px; line-height: 22px; font-weight: 400;
  }
  .service__text { position: absolute; left: 21px; top: 16px; right: 8px; font-size: 13.5px; line-height: 17px; }

  .footnotes {
    position: absolute; left: 40px; right: 40px; top: 1046px;
    text-align: center; font-size: 11.5px; line-height: 15px;
  }
  .footnotes p + p { margin-top: 10px; }

  .contact-bar { position: absolute; left: 0; top: 1117px; width: 840px; height: 53px; }
  .contact-bar svg.contact-bar__bg { position: absolute; inset: 0; }
  .contact-item {
    position: absolute; top: 0; height: 53px;
    display: flex; align-items: center; gap: 14px;
    color: #fff; font-size: 17px; letter-spacing: 0.3px; white-space: nowrap;
  }
  .contact-item--phone { left: 98px; }
  .contact-item--mail { left: 326px; }
  .contact-item--web { left: 566px; }
</style>
</head>
<body>
<main class="flyer">

  <div class="brand-mark">
    <div class="brand-mark__dot"></div>
    <div class="brand-mark__name">VENTRA</div>
  </div>

  <h1 class="headline-brand">VENTRA</h1>
  <p class="tagline">Nachwuchsförderung und <span class="tagline__accent">-mangement</span></p>

  <div class="claim">
    <div class="claim__top">WIR BEGLEITEN DICH</div>
    <div class="claim__mid">auf deinem</div>
    <div class="claim__bottom">Weg zum Profi</div>
  </div>

  <div class="hero-figure" role="img" aria-label="Farbenfrohe Silhouette eines Fußballspielers mit Ball"></div>

  <section class="service service--left service--row1">
    <h2 class="service__title">Karriereplanung</h2>
    <p class="service__text">Wir haben deine Karriere im Blick! In enger Absprache<br>mit deinen Eltern und dir leiten wir die richtigen<br>Maßnahmen und Schrtitte ein, um dein Ziel „<br>Profifußballer“ zu realisieren.</p>
  </section>
  <section class="service service--right service--row1">
    <h2 class="service__title">Ausrüstung</h2>
    <p class="service__text">Wir besorgen dir deine Ausrüstung! Unsere<br>Beziehungen zu den großen Sportartikelherstellern<br>ermöglichen den Abschluss von Ausrüsterverträgen*.</p>
  </section>
  <section class="service service--left service--row2">
    <h2 class="service__title">Ständiger Ansprechpartner</h2>
    <p class="service__text">Egal um welchen Themen es sich handelt, wir sind für<br>dich da! Ein vertrauensvolles und freundschaftliches<br>Verhältnis ist uns besonders wichtig.</p>
  </section>
  <section class="service service--right service--row2">
    <h2 class="service__title">Vorsorge</h2>
    <p class="service__text">Verletzungen gehören leider zum Fußball dazu.<br>Wir sichern dich ab, indem wir eine private<br>Zusatzkrankenversicherung für dich abschließen.</p>
  </section>
  <section class="service service--left service--row3">
    <h2 class="service__title">Rechtsberatung/Vertragsrecht</h2>
    <p class="service__text">Juristendeutsch und Kleingedrucktes? Kein Problem!<br>Wir helfen dir den Durchblick zu behalten und holen<br>immer das Beste für dich raus.</p>
  </section>
  <section class="service service--right service--row3">
    <h2 class="service__title">Kooperationspartner/Netzwerk</h2>
    <p class="service__text">Ob Entscheidungsträger oder Experte, wir kennen die<br>richtigen Leute. Zusätzlich bieten wir dir eine große<br>Bandbreite an Leistungen, die du jederzeit in Anspruch<br>nehmen kannst**.</p>
  </section>

  <div class="footnotes">
    <p>*Die Entscheidung über das Zustandekommen eines Ausrüstervertrags obliegt dem jeweiligen Sportartikelhersteller. Ist ein Abschluss<br>aktuell nicht möglich, erhältst du von uns 2x pro Saison neue Fußballschuhe sowie weitere Ausrüstungsgegenstände.</p>
    <p>**Personal Training, Athletik-Training, Ernährungsberatung, Sportpsychologische Betreuung, uvm.</p>
  </div>

  <footer class="contact-bar">
    <svg class="contact-bar__bg" width="840" height="53" viewBox="0 0 840 53">
      <polygon points="0,0 294,0 270,53 0,53" fill="var(--footer-black)"/>
      <polygon points="300,0 840,0 840,53 276,53" fill="var(--footer-blue)"/>
    </svg>
    <div class="contact-item contact-item--phone">
      <svg width="16" height="16" viewBox="0 0 24 24" fill="none" stroke="var(--footer-blue)" stroke-width="2.2"><path d="M5 3h4l2 5-2.5 1.5a11 11 0 0 0 6 6L16 13l5 2v4a2 2 0 0 1-2 2A16 16 0 0 1 3 5a2 2 0 0 1 2-2z"/></svg>
      <span>07131/4820157</span>
    </div>
    <div class="contact-item contact-item--mail">
      <svg width="16" height="12" viewBox="0 0 16 12"><rect x="0.5" y="0.5" width="15" height="11" fill="none" stroke="#1c1c1c"/><path d="M0.5 0.5 8 7l7.5-6.5" fill="none" stroke="#1c1c1c"/></svg>
      <span>info@ventra-sport.de</span>
    </div>
    <div class="contact-item contact-item--web">
      <svg width="14" height="14" viewBox="0 0 14 14" fill="none" stroke="#1c1c1c" stroke-width="1.2"><circle cx="7" cy="7" r="6"/><ellipse cx="7" cy="7" rx="2.6" ry="6"/><path d="M1 7h12"/></svg>
      <span>www.ventra-sport.de</span>
    </div>
  </footer>

</main>
</body>
</html>
```